Accounting firm needing business card / letterhead designed
Marcus L. Trenholm, CPA
marcus@veltrowledger.com
www.veltrowledger.com
842 E Alder Ave Brackton, VT 43827
555-562-0974

```html
<!DOCTYPE html>
<html lang="en">
<head>
<meta charset="utf-8">
<title>Veltrow Ledger — Business Card</title>
<link href="https://fonts.googleapis.com/css2?family=Michroma&family=Orbitron:wght@700&family=Roboto:wght@400&display=swap" rel="stylesheet">
<style>
  :root {
    --backdrop: #c4c4c4;
    --card-white: #f4f4f4;
    --brand-navy: #2a2766;
    --brand-green: #8dc63f;
    --text-grey: #555555;
    --text-white: #ffffff;
  }
  * { margin: 0; padding: 0; box-sizing: border-box; }
  html, body {
    width: 1200px;
    height: 960px;
    overflow: hidden;
    background: var(--backdrop);
  }
  .canvas {
    position: relative;
    width: 1200px;
    height: 960px;
  }
  .card {
    position: absolute;
    width: 600px;
    height: 342px;
    border-radius: 16px;
  }
  .card--front {
    left: 320px;
    top: 100px;
    background: var(--card-white);
  }
  .card--back {
    left: 320px;
    top: 493px;
    background: var(--brand-green);
  }
  .brand-name {
    position: absolute;
    left: 0;
    right: 0;
    top: 150px;
    text-align: center;
    font-family: "Michroma", sans-serif;
    font-size: 27px;
    letter-spacing: 1px;
    color: var(--brand-navy);
  }
  .front-web {
    position: absolute;
    left: 0;
    right: 0;
    top: 288px;
    text-align: center;
    font-family: "Roboto", sans-serif;
    font-size: 14px;
    letter-spacing: 6.5px;
    color: var(--text-grey);
  }
  .holder-name {
    position: absolute;
    left: 32px;
    top: 33px;
    font-family: "Orbitron", sans-serif;
    font-weight: 700;
    font-size: 16px;
    letter-spacing: 0.5px;
    color: var(--text-white);
    text-transform: uppercase;
  }
  .divider {
    position: absolute;
    left: 45px;
    top: 255px;
    width: 518px;
    height: 2px;
  }
  .contact {
    position: absolute;
    right: 35px;
    top: 273px;
    text-align: right;
    font-family: "Roboto", sans-serif;
    font-style: normal;
    font-size: 14px;
    line-height: 21px;
    color: var(--text-white);
  }
</style>
</head>
<body>
<main class="canvas">
  <section class="card card--front">
    <p class="brand-name">VELTROW LEDGER</p>
    <p class="front-web">www.veltrowledger.com</p>
  </section>

  <section class="card card--back">
    <h1 class="holder-name">Marcus L. Trenholm, CPA</h1>
    <svg class="divider" viewBox="0 0 518 2" preserveAspectRatio="none" aria-hidden="true">
      <defs>
        <linearGradient id="divider-fade" x1="0" x2="1" y1="0" y2="0">
          <stop offset="0" stop-color="#ffffff" stop-opacity="0"/>
          <stop offset="1" stop-color="#ffffff" stop-opacity="1"/>
        </linearGradient>
      </defs>
      <rect width="518" height="2" fill="url(#divider-fade)"/>
    </svg>
    <address class="contact">
      842 E Alder Ave, Brackton, VT 43827<br>
      C: 555-562-0974 E: marcus@veltrowledger.com W: www.veltrowledger.com
    </address>
  </section>
</main>
</body>
</html>
```